Redesign two existing website pages and one new landing page for dental office

I need to redesign two webpages on my dental website, the Home page (http://velbridgedental.com) and the Dental Implant Services page (http://www.velbridgedental.com/dental-implant-services) and also create a landing page for the Dental Implant Services page.

Please use the same color scheme, slogans and subtitles for the redesign pages and create a reserved video spot on each page. The video spots should not be too big but not too small either and positioned in a central key location on each of the pages. The final redesigned pages should communicate leadership, confidence and trust.

The new landing page for the Dental implant Services page must not have any hyperlinks on the page and must entice the viewer to give name and email before downloading a "Free" eBook called "Is a Fuller Smile Worth the Wait?" Any added photo images to this new page must be smiling.
Updates

Project Deadline Extended Reason: I got feedback that my project was not long enough so I'm extending it by 5 days. Added Thursday, April 16, 2015

Target Market(s)

People who are middle-age to seniors.

Industry/Entity Type

Dental

Coding

Coded - Design and coding required

Number of Pages Required

3 page

Requirements
Must have
• Compatible with existing website colors and theme.

```html
<!DOCTYPE html>
<html lang="en">
<head>
<meta charset="utf-8">
<title>Services | Velbridge Dental Care</title>
<link href="https://fonts.googleapis.com/css2?family=Open+Sans:wght@300;400;600;700&display=swap" rel="stylesheet">
<style>
:root{
  --brand:#3f8f8c;
  --ink:#333;
  --body:#555;
  --muted:#888;
  --panel:#ebebeb;
  --menu-dark:#5a5a5a;
  --menu-light:#ececec;
  --accent:#3ea6dc;
  --hero-a:#4f6b2c;
  --hero-b:#a4b86a;
  --footer:#e6e6e6;
  --video:#2f3b3b;
}
*{box-sizing:border-box;margin:0;padding:0}
html,body{width:1200px;height:2720px;overflow:hidden}
body{font-family:"Open Sans",Arial,sans-serif;color:var(--body);background:#fff;font-size:12.5px;line-height:19px;position:relative}
.wrap{width:870px;margin:0 auto;position:relative}

.site-header{height:75px;background:#fff}
.site-header .wrap{height:75px;display:flex;align-items:center;justify-content:space-between}
.brand{display:flex;align-items:center;gap:10px;color:var(--brand);font-size:24px;font-weight:600}
.brand-mark{width:22px;height:22px;border-radius:50%;background:var(--brand)}
.main-nav{display:flex;gap:22px;font-size:13px;color:var(--ink);padding-top:22px}

.page-title{height:120px;background:linear-gradient(#f4f4f4,#dcdcdc)}
.page-title h1{font-weight:300;font-size:40px;color:var(--ink);line-height:120px;padding-left:10px}

.intro{height:490px;position:relative}
.intro-text{width:440px;padding:12px 0 0 0}
.intro-text h2{font-size:17px;line-height:23px;color:var(--ink);font-weight:600;margin-bottom:14px}
.intro-text p{margin-bottom:12px}
.video-spot{float:right;width:220px;height:126px;margin:2px 0 8px 14px;background:linear-gradient(135deg,#3d4a4a,var(--video));display:flex;flex-direction:column;align-items:center;justify-content:center;gap:6px;color:#dfe7e7;font-size:11px}
.service-menu{position:absolute;left:630px;top:6px;width:560px;list-style:none}
.service-menu li{height:81px;line-height:81px;padding-left:40px;font-size:21px;color:var(--ink);background:var(--menu-light);border-bottom:1px solid #fff}
.service-menu li.is-active{background:var(--menu-dark);color:#fff}

.lead-hero{height:400px;position:relative;background:linear-gradient(100deg,var(--hero-a),#7e9648 55%,var(--hero-b));overflow:hidden}
.hero-photo{position:absolute;right:0;top:0;width:380px;height:400px;background:linear-gradient(90deg,rgba(199,154,134,0),#c79a86 30%,#9c7764)}
.lead-form{position:absolute;left:264px;top:62px;width:666px;text-align:center}
.lead-form h2{color:#fff;font-size:21px;font-weight:400;letter-spacing:.5px;margin-bottom:28px;white-space:nowrap}
.field-row{display:flex;gap:24px;margin-bottom:16px}
.field{flex:1;height:42px;border:1px solid rgba(255,255,255,.7);background:rgba(255,255,255,.12);color:#fff;text-align:left;padding-left:14px;line-height:40px;font-size:13px}
.btn{display:inline-block;margin-top:6px;width:192px;height:40px;line-height:40px;background:var(--accent);color:#fff;font-size:16px}

.details{padding-top:14px}
.details .wrap{display:flex;gap:20px}
.problems{width:425px;height:730px;background:var(--panel);padding:22px 20px}
.problems h2{font-size:19px;line-height:26px;color:var(--ink);font-weight:600;margin-bottom:14px}
.problems p{margin-bottom:14px}
.urgency{width:425px;padding-top:4px}
.urgency h2{font-size:17px;color:var(--ink);font-weight:600;margin-bottom:16px}
.urgency h3{font-size:14px;color:var(--ink);font-weight:600;margin-bottom:6px}
.urgency p{margin-bottom:14px}

.treatments{padding-top:26px}
.treatments h3{font-size:15px;color:var(--ink);font-weight:600;margin-bottom:12px}
.treatments p{margin-bottom:14px}
.treatment-photo{float:right;width:200px;height:100px;margin:0 0 10px 20px;background:linear-gradient(135deg,#fafafa,#d9d9d9)}
.clear{clear:both}

.site-footer{position:absolute;left:0;top:2466px;width:1200px;height:254px;background:var(--footer)}
.footer-nav{display:flex;justify-content:space-between;width:780px;margin:0 auto;padding-top:26px;font-size:13px;color:var(--muted)}
.footer-rule{width:870px;margin:22px auto 0;border-top:1px solid #ccc}
.footer-bottom{width:870px;margin:100px auto 0;display:flex;justify-content:space-between;align-items:center;font-size:10px;color:var(--muted)}
.social{display:flex;gap:8px}
.social span{width:14px;height:14px;border-radius:50%;background:#999}
</style>
</head>
<body>
<header class="site-header">
  <div class="wrap">
    <div class="brand"><span class="brand-mark"></span>Velbridge Dental Care</div>
    <nav class="main-nav"><span>Home</span><span>About Us</span><span>Dental</span><span>Services</span><span>Blog</span><span>Testimonials</span><span>Contact Us</span></nav>
  </div>
</header>

<section class="page-title"><div class="wrap"><h1>Services</h1></div></section>

<section class="intro">
  <div class="wrap">
    <div class="intro-text">
      <h2>Dr. Owen Hale: The Cedar Hollow Cosmetic Dentist Giving Attractive Smile Makeovers with Dental Implants</h2>
      <div class="video-spot" role="img" aria-label="Reserved video spot about dental implants">
        <svg width="40" height="40" viewBox="0 0 40 40"><circle cx="20" cy="20" r="18" fill="none" stroke="#fff" stroke-width="2"/><path d="M16 12 L29 20 L16 28 Z" fill="#fff"/></svg>
        <span>Watch: Dental Implants</span>
      </div>
      <p>Are you suffering from severe tooth decay? Are your teeth badly damaged? Do you have missing teeth? These are some of the reasons why people do not flash their pearly whites in public. If you can identify with such people, it is time to enjoy the affordable and exceptional dental implant services of Dr. Owen Hale, DDS FAGD.</p>
      <p>Velbridge Dental Care has been successfully serving Cedar Hollow TX for several years, restoring smiles at our dental implant center. Dr. Hale has been dedicated to providing attractive new smiles to his patients using the latest techniques in dental implants. If you are looking to regain a natural smile that showcases bright white teeth, look no further than dental implants with Dr. Hale.</p>
    </div>
  </div>
  <ul class="service-menu">
    <li class="is-active">Dental Hygiene</li>
    <li>Dental Emergency</li>
    <li>Dental Implants</li>
    <li>Cosmetic Dentistry</li>
    <li>Beautiful Dentures</li>
    <li>Sedation Dentistry</li>
  </ul>
</section>

<section class="lead-hero">
  <div class="hero-photo" role="img" aria-label="Smiling woman outdoors with greenery behind her"></div>
  <div class="lead-form">
    <h2>GET MORE INFO ABOUT DENTAL IMPLANTS</h2>
    <div class="field-row"><div class="field">First Name</div><div class="field">Last Name</div></div>
    <div class="field-row"><div class="field">Cell Phone number</div><div class="field">Email</div></div>
    <div class="btn">Get More Info!</div>
  </div>
</section>

<section class="details">
  <div class="wrap">
    <div class="problems">
      <h2>What Problems Can Dental Implants Address?</h2>
      <p>You will be surprised to learn dental implants can help correct several teeth related problems. Some of the conditions when dental implants are used include:</p>
      <p>Replacing many missing teeth instead of wearing dentures or removable bridges. Replacing teeth that have been irreparably damaged from trauma or tooth decay. Replacing loose teeth that are loose and have poor bone support due to gum disease infection. An exchange for poorly fitting dentures, which are loose or painful and may result in a socially embarrassing moment due to displacement. These ill-fitting dentures often cause the supporting bone to shrivel and shrink with time.</p>
      <p>Dr. Hale emphatically believes dental implants are an effective and permanent solution for restoring teeth when giving his patients a smile makeover. Thanks to the advances in modern implant dentistry, Dr. Hale is equipped to provide all his patients with attractive new smiles that look natural and beautiful.</p>
      <p>You will be amazed at how dental implants can not only transform your smile, but also make you look youthful, self-confident and attractive.</p>
      <p>If you want to find out more about how Dr. Hale can help you through his wide range of cosmetic dentistry services, call (555) 014-2290 today to schedule a complimentary consultation. Alternatively, you can visit Velbridge Dental Care website to get more information on dental implants and other cosmetic dentistry services.</p>
    </div>
    <div class="urgency">
      <h2>Don't Wait 'til it Hurts!</h2>
      <h3>Understanding Dental Implants</h3>
      <p>Dental implants have truly revolutionized smile reconstruction. Missing teeth, severely damaged teeth and extreme tooth decay can easily be treated with the help of these implants and restore people's self-confidence and self-esteem.</p>
      <p>When the dental implant procedure is performed accurately and correctly, the results can be astonishing. No one will know you have implants, even when you flash a smile.</p>
      <p>A dental implant consists of a small titanium post or screw that is surgically implanted into your jawbone. After dental implant placement, and a few months recuperation period, the surface of the implant fuses with your jawbone. The result is a sturdy and strong base which can be used as an anchor for attaching a dental prosthesis such as a crown, a fixed bridge or a denture.</p>
      <p>Dr. Hale has helped hundreds of clients regain their self-confidence and beautiful smiles with the help of dental implants. So, if you are looking for an experienced and skilled dental implant dentist in Cedar Hollow TX, your search ends with Dr. Owen Hale.</p>
      <h3>Single Tooth Dental Implants Restored with a Crown</h3>
      <p>Accidents and periodontal diseases cause people to lose a single tooth. If you have lost a single tooth, it is possible to replace it using a dental implant. A dental implant makes sure that the original structure of the tooth is retained without any gaps. The dentist places the dental implant in the gap created by the missing tooth. After the implant is placed in the jawbone, a small post known as abutment is fixed onto it. The porcelain crown, which looks and works like a natural tooth, is then fixed on the abutment using dental cement.</p>
    </div>
  </div>
</section>

<section class="treatments">
  <div class="wrap">
    <h3>Multiple Teeth Dental Implants Restored with a Fixed Bridge</h3>
    <p>For various reasons, people start losing multiple teeth after a certain age. Multiple dental implants are one of the best options for such people. Multiple tooth loss is common among aging people or those who have sustained a trauma on the mouth. Even with good dental hygiene, it is possible to lose teeth gradually. Having too many missing teeth is detrimental to your confidence at any age. Several missing teeth can result in speech impairment and digestive problems, as the person will be unable to chew their food properly. Dental implants offer an ideal solution for such a problem, as they improve the appearance of the person and this results in better self-confidence and self-image.</p>
    <p>After examining the structure and the condition of the jawbone, it may be necessary for a dentist to perform AO4 or All-on-Four treatment. Bone deterioration typically takes place under the gums and is barely noticeable. If there is such a condition then this treatment is essential, as the bone will not be able to support dental implants.</p>
    <h3 style="margin-top:22px">All-On-Four (AO4) Dental Implants Restored with a Screw Retained Denture</h3>
    <div class="treatment-photo" role="img" aria-label="Illustration of a full arch denture on four implants"></div>
    <p>The all-on-4 upper jaw/The AO4 is a permanent solution to replace all the teeth in the mouth. It makes use of a denture-like arched structure for both the upper and lower jaw. This treatment is done using 4 posts for each jaw (upper and lower). You may wonder why should there are 4 posts. Many dentists find this as an optimal number to provide a permanent solution for missing teeth. A bridge can be sturdily placed on to the jawbone using these four posts. The four points provide the support columns for the teeth structure and they also help to take the load of the denture.</p>
    <div class="clear"></div>
    <div class="treatment-photo" role="img" aria-label="Illustration of a lower arch bridge on implants" style="margin-top:8px"></div>
    <p style="margin-top:12px">all-on-4 lower jaw/All-on-four implants are very similar to the concept of roadway bridges. Just like a bridge is supported using columns at frequent intervals, even the dental bridges use four posts to support each bridge. These dental implants can give you a smile makeover and restore the lost function of your teeth. You will be able to chew, speak clearly, bite and smile without feeling self-conscious.</p>
    <div class="clear"></div>
    <p>Different types of dental implants can give you a lasting set of teeth and keep you smiling for the rest of your life. Do not let lost teeth reduce the quality of your life or lower your self-esteem. Instead opt for dental implants and transform</p>
  </div>
</section>

<footer class="site-footer">
  <nav class="footer-nav"><span>Home</span><span>About Us</span><span>Dental</span><span>Services</span><span>Blog</span><span>Testimonials</span><span>Contact Us</span></nav>
  <div class="footer-rule"></div>
  <div class="footer-bottom">
    <p class="copyright">©2014 Velbridge Dental Care, Harbor Oak Medical Plaza, 480 Linden Road, Ste #210, Cedar Hollow, TX 77001</p>
    <div class="social"><span></span><span></span><span></span><span></span><span></span></div>
  </div>
</footer>
</body>
</html>
```